Brell Stone Company Business Cards

Front and Back Business Card - logo and text setup - cool design. I need workable photoshop or illustrator files so I can setup each employee card with design that is created
Updates

Hi everyone, thank you for the great entries. Please no more white and blue cards - there are so many already - black and silver only now please. thanks!

Target Market(s)

Construction Industry - Facility Managers

Industry/Entity Type

Construction

Contact Information for Business Card

I really like contemporary simplistic looks - clean neat....not opposed to seeing some black backrounds

Requirements
Must have
• Logo/website address with design on front only - www.brellstone-example.com (logo attached)
• Back:
• Name/Title/Company Address/Phone/email address
Nice to have
• Cool design
Should not have
• Nothing gimmicky like Fire or Water - since we are a Fire Protection company - it has all been done

```html
<!DOCTYPE html>
<html lang="en">
<head>
<meta charset="utf-8">
<title>Brell Stone Company Business Cards</title>
<link href="https://fonts.googleapis.com/css2?family=Open+Sans:wght@400;600;700&display=swap" rel="stylesheet">
<style>
  :root {
    --stage: #c9cdd1;
    --card: #000000;
    --brand-blue: #0625a3;
    --brand-red: #ff2121;
    --text-light: #ffffff;
    --logo-grey: #7a7a7a;
    --divider: #3a3a3a;
  }
  * { margin: 0; padding: 0; box-sizing: border-box; }
  html, body {
    width: 1200px; height: 1193px; overflow: hidden;
    background: var(--stage);
    font-family: "Open Sans", sans-serif;
  }
  .canvas { position: relative; width: 1200px; height: 1193px; }
  .card {
    position: absolute;
    background: var(--card);
    overflow: hidden;
    color: var(--text-light);
  }
  .card--front { left: 61px; top: 84px; width: 872px; height: 498px; border-radius: 26px; }
  .card--back { left: 264px; top: 633px; width: 873px; height: 499px; border-radius: 42px; }

  .front__band {
    position: absolute; left: 0; right: 0; top: 382px; bottom: 0;
    background: linear-gradient(90deg, var(--brand-red) 0%, #7a2060 40%, var(--brand-blue) 70%);
  }
  .front__company {
    position: absolute; left: 86px; top: 165px; width: 400px;
    font-size: 42px; font-weight: 700; line-height: 1.1;
    color: var(--brand-blue);
  }
  .front__divider {
    position: absolute; left: 502px; top: 117px;
    width: 2px; height: 178px; background: var(--divider);
  }
  .contact { position: absolute; left: 528px; top: 116px; list-style: none; }
  .contact__item {
    display: flex; align-items: center; gap: 9px;
    font-size: 19px; line-height: 38.5px; white-space: nowrap;
  }
  .contact__icon { width: 20px; height: 20px; flex: none; }
  .address {
    position: absolute; left: 532px; top: 233px;
    font-size: 22px; line-height: 35px; font-style: normal;
  }
  .person {
    position: absolute; left: 584px; top: 410px; width: 240px; text-align: center;
  }
  .person__name { font-size: 33px; font-weight: 700; line-height: 1.2; white-space: nowrap; }
  .person__title { font-size: 29px; font-weight: 400; line-height: 1.25; }

  .back__company {
    position: absolute; left: 0; right: 0; top: 186px;
    text-align: center; font-size: 52px; font-weight: 700;
    color: var(--logo-grey);
  }
  .back__web {
    position: absolute; left: 0; right: 0; top: 320px;
    text-align: center; font-size: 26px; letter-spacing: 5px;
  }
</style>
</head>
<body>
<main class="canvas">

  <section class="card card--front" aria-label="Business card front">
    <div class="front__band" role="img" aria-label="Decorative red and blue band"></div>

    <div class="front__company">Brell Stone Company</div>
    <div class="front__divider"></div>

    <ul class="contact">
      <li class="contact__item">
        <svg class="contact__icon" viewBox="0 0 24 24" aria-hidden="true"><path fill="var(--brand-red)" d="M6.6 10.8a15.1 15.1 0 0 0 6.6 6.6l2.2-2.2a1 1 0 0 1 1-.25 11.4 11.4 0 0 0 3.6.57 1 1 0 0 1 1 1V20a1 1 0 0 1-1 1A17 17 0 0 1 3 4a1 1 0 0 1 1-1h3.5a1 1 0 0 1 1 1c0 1.25.2 2.45.57 3.57a1 1 0 0 1-.25 1Z"/></svg>
        (555) 014-2278
      </li>
      <li class="contact__item">
        <svg class="contact__icon" viewBox="0 0 24 24" aria-hidden="true"><rect x="2" y="5" width="20" height="14" fill="var(--brand-red)"/><path d="M2 5l10 8 10-8M2 19l7-7M22 19l-7-7" stroke="#000" stroke-width="1.6" fill="none"/></svg>
        info@brellstone-example.com
      </li>
      <li class="contact__item">
        <svg class="contact__icon" viewBox="0 0 24 24" aria-hidden="true"><g fill="none" stroke="var(--brand-red)" stroke-width="1.6"><circle cx="12" cy="12" r="10"/><ellipse cx="12" cy="12" rx="4.5" ry="10"/><path d="M2 12h20M4 7h16M4 17h16"/></g></svg>
        www.brellstone-example.com
      </li>
    </ul>

    <address class="address">48 Harbor Works Lane<br>Millbrook, NY 10000</address>

    <div class="person">
      <div class="person__name">Dana Whitfield</div>
      <div class="person__title">President</div>
    </div>
  </section>

  <section class="card card--back" aria-label="Business card back">
    <div class="back__company">Brell Stone Company</div>
    <div class="back__web">www.brellstone-example.com</div>
  </section>

</main>
</body>
</html>
```